Business Card Design - Amberfield Court

We are looking at a new design for our business cards that has a modern and professional look. We run a residential aged care facility focussing on the care of residents. The cards will be used for potential clients, consultants and business opportunities in this sector. Blue and white is our main colours and would to see these colours incorporated in the design.
Industry/Entity Type
Business
Contact Information for Business Card
Amberfield Court, Darren Walsh, dwalsh@amberfieldcourt.com.au, Finance Manager, 0472 639 208, BCom, 37 Marrabel Crescent, Brindle Vale, Qld 4093.
Look and feel
Each slider illustrates characteristics of the customer's brand and the style your logo design should communicate.

```html
<!DOCTYPE html>
<html lang="en">
<head>
<meta charset="utf-8">
<title>Amberfield Court – Business Card</title>
<link rel="stylesheet" href="https://fonts.googleapis.com/css2?family=Arimo:wght@400;700&display=swap">
<style>
  :root {
    --page: #e9e7e4;
    --brand-blue: #47738d;
    --brand-blue-light: #5f8ba4;
    --brand-blue-dark: #3a627a;
    --taupe: #a09289;
    --ink: #2f2f2f;
    --card-white: #ffffff;
    --rule: #cfcfcf;
  }
  * { box-sizing: border-box; margin: 0; padding: 0; }
  html, body { width: 1200px; height: 950px; overflow: hidden; }
  body {
    background: var(--page);
    font-family: "Arimo", Arial, sans-serif;
    display: flex;
    flex-direction: column;
    align-items: center;
    justify-content: center;
    gap: 40px;
  }
  .card {
    width: 735px;
    height: 420px;
    position: relative;
    overflow: hidden;
    box-shadow: 0 6px 18px rgba(0,0,0,0.18);
  }

  /* Back of card */
  .card--back {
    background: linear-gradient(135deg, var(--brand-blue-dark), var(--brand-blue-light));
    display: flex;
    flex-direction: column;
    align-items: center;
    justify-content: center;
    gap: 26px;
    color: var(--card-white);
  }
  .back-brand {
    display: flex;
    align-items: center;
    gap: 16px;
    font-size: 40px;
    font-weight: 400;
    letter-spacing: 1px;
  }
  .back-brand .mark-dot {
    width: 34px; height: 34px; border-radius: 50%;
    background: var(--card-white);
  }
  .back-web { font-size: 20px; letter-spacing: 1px; }

  /* Front of card */
  .card--front { background: var(--card-white); }
  .front-band {
    position: absolute; left: 0; right: 0; bottom: 0;
    height: 32px;
    background: var(--brand-blue);
  }
  .front-brand {
    position: absolute;
    left: 30px; top: 0; width: 300px; height: 388px;
    display: flex; align-items: center; justify-content: center; gap: 12px;
    color: var(--brand-blue);
    font-size: 27px;
    font-weight: 400;
  }
  .front-brand .mark-dot {
    width: 22px; height: 22px; border-radius: 50%;
    background: var(--brand-blue);
    flex: none;
  }
  .divider {
    position: absolute;
    left: 348px; top: 80px;
    width: 1px; height: 240px;
    background: var(--rule);
  }
  .contact {
    position: absolute;
    left: 378px; top: 86px;
    color: var(--ink);
  }
  .contact__name {
    color: var(--brand-blue);
    font-size: 27px;
    font-weight: 700;
  }
  .contact__name small { font-size: 18px; font-weight: 700; }
  .contact__role {
    color: var(--taupe);
    font-size: 18px;
    margin: 4px 0 16px;
  }
  .contact__address { font-size: 18px; line-height: 1.3; margin-bottom: 10px; }
  .contact__list { list-style: none; font-size: 18px; line-height: 1.45; }
  .contact__list li { display: flex; align-items: center; gap: 10px; }
  .contact__list svg { width: 16px; height: 16px; flex: none; fill: var(--ink); }
</style>
</head>
<body>

  <section class="card card--back" aria-label="Card back">
    <div class="back-brand"><span class="mark-dot"></span>Amberfield Court</div>
    <div class="back-web">www.amberfieldcourt.com.au</div>
  </section>

  <section class="card card--front" aria-label="Card front">
    <div class="front-brand"><span class="mark-dot"></span>Amberfield Court</div>
    <div class="divider"></div>
    <div class="contact">
      <p class="contact__name">Darren Walsh <small>BCom</small></p>
      <p class="contact__role">Finance Manager</p>
      <p class="contact__address">37 Marrabel Crescent<br>Brindle Vale, Qld 4093.</p>
      <ul class="contact__list">
        <li>
          <svg viewBox="0 0 16 16" aria-hidden="true"><path d="M1 5c0-2 3-3 7-3s7 1 7 3v1h-3V5H4v1H1z"/><rect x="3" y="7" width="10" height="7" rx="1"/></svg>
          0472 639 208
        </li>
        <li>
          <svg viewBox="0 0 16 16" aria-hidden="true"><rect x="1" y="3" width="14" height="10" rx="1"/><path d="M1.5 3.5 8 9l6.5-5.5" fill="none" stroke="#fff" stroke-width="1.3"/></svg>
          dwalsh@amberfieldcourt.com.au
        </li>
        <li>
          <svg viewBox="0 0 16 16" aria-hidden="true"><circle cx="8" cy="8" r="7"/><path d="M1 8h14M8 1c-3 3-3 11 0 14M8 1c3 3 3 11 0 14" fill="none" stroke="#fff" stroke-width="1"/></svg>
          www.amberfieldcourt.com.au
        </li>
      </ul>
    </div>
    <div class="front-band"></div>
  </section>

</body>
</html>
```